Revamp Marketing Website For Video Production Website

need to revamp current website www.kestrelfilmstudio.net
reference sites www.vantora.net & http://layoutcrate.net/kestrel/
Use all current content on current kestrel website. I want a revamped modenr look. Sometbing that wows customers.
reference site www.vantora.net
Target Market(s)
business owners
Industry/Entity Type
Video Production
Number of Pages Required
5+ page
Colors
Designer to choose colors to be used in the design.
Requirements
Must have
- need to revamp current website www.kestrelfilmstudio.net
- reference sites www.vantora.net & http://layoutcrate.net/kestrel/
- Use all current content on current kestrel website. I want a revamped modenr look. Sometbing that wows customers.
- reference site www.vantora.net
Nice to have
Should not have

```html
<!DOCTYPE html>
<html lang="en">
<head>
<meta charset="utf-8">
<title>Kestrel — Marketing Videos Made For You</title>
<link rel="stylesheet" href="https://fonts.googleapis.com/css2?family=Montserrat:wght@400;500;600;700&display=swap">
<style>
  :root {
    --blue: #0c8fd0;
    --blue-light: #33b6ee;
    --navy: #141a2b;
    --navy-card: #101626;
    --ice: #eaf5fc;
    --ink: #14171f;
    --grey: #9a9ea6;
    --white: #ffffff;
    --line: #4fb0e0;
  }
  * { box-sizing: border-box; margin: 0; padding: 0; }
  html, body { width: 1200px; height: 4115px; overflow: hidden; }
  body { font-family: "Montserrat", sans-serif; color: var(--ink); background: var(--white); }
  .page { position: relative; width: 1200px; height: 4115px; overflow: hidden; }
  .abs { position: absolute; }
  .photo { position: absolute; }

  /* hero */
  .hero { position: absolute; left: 0; top: 0; width: 1200px; height: 678px;
    background: linear-gradient(160deg, #2b3447 0%, #222a3a 45%, #3a4030 100%); }
  .brand { position: absolute; display: flex; flex-direction: column; color: var(--white); }
  .brand-name { font-weight: 700; font-size: 30px; letter-spacing: 3px; line-height: 1; display: flex; align-items: center; gap: 8px; }
  .brand-name::before { content: ""; width: 14px; height: 14px; background: var(--blue-light); border-radius: 50%; }
  .brand-tag { font-weight: 600; font-size: 9.5px; letter-spacing: .3px; margin-top: 6px; }
  .nav a { position: absolute; top: 47px; font-size: 15px; color: #d0d4dc; text-decoration: none; }
  .nav a.active { color: var(--blue-light); font-weight: 600; }
  .nav-caret { position: absolute; left: 415px; top: 70px; width: 0; height: 0;
    border-left: 6px solid transparent; border-right: 6px solid transparent; border-bottom: 9px solid var(--blue-light); }
  .btn { position: absolute; display: flex; align-items: center; justify-content: center; gap: 14px;
    color: var(--white); font-weight: 500; border-radius: 3px;
    background: linear-gradient(90deg, var(--blue-light), #1aa1e4); }
  .hero-title { left: 78px; top: 206px; width: 420px; font-size: 44px; font-weight: 700; line-height: 58px; letter-spacing: -.5px; color: var(--white); }
  .hero-sub { left: 78px; top: 388px; font-size: 30px; font-weight: 500; color: var(--white); }

  /* channels */
  .channels { position: absolute; left: 0; top: 678px; width: 1200px; height: 353px; background: var(--ice); }
  .channels h2 { position: absolute; left: 78px; top: 92px; font-size: 30px; font-weight: 600; line-height: 42px; width: 400px; }
  .dot { position: absolute; border-radius: 50%; box-shadow: 0 6px 14px rgba(0,0,0,.15); }

  /* promote */
  .promote-title { left: 78px; top: 1262px; font-size: 42px; font-weight: 700; letter-spacing: -.5px; }
  .promote-kicker { left: 78px; top: 1318px; font-size: 22px; font-weight: 600; color: var(--blue); }
  .promote-copy { left: 78px; top: 1351px; width: 460px; font-size: 13px; line-height: 26px; color: var(--grey); }

  /* examples */
  .examples { position: absolute; left: 0; top: 1625px; width: 1200px; height: 521px; background: var(--blue); color: var(--white); }
  .section-title { font-size: 40px; font-weight: 700; letter-spacing: -1px; }
  .topics li { position: absolute; list-style: none; font-size: 16px; font-weight: 500; padding-left: 22px; }
  .topics li::before { content: ""; position: absolute; left: 0; top: 7px; width: 9px; height: 9px; background: var(--white); border-radius: 50%; }
  .thumb { position: absolute; border: 5px solid var(--white); }
  .arrow { position: absolute; width: 40px; height: 40px; border-radius: 50%; background: var(--white); display: flex; align-items: center; justify-content: center; }

  /* features */
  .feature { position: absolute; width: 300px; text-align: center; }
  .feature .icon { width: 93px; height: 93px; margin: 0 auto; border-radius: 4px; background: var(--navy); display: flex; align-items: center; justify-content: center; }
  .feature .icon.accent { background: linear-gradient(160deg, var(--blue-light), #1a9fe0); }
  .feature h3 { margin-top: 36px; font-size: 18px; font-weight: 600; }
  .feature h3.accent { color: var(--blue); }
  .feature p { margin-top: 10px; padding: 0 12px; font-size: 13px; line-height: 26px; color: var(--grey); }

  /* sizes */
  .sizes { position: absolute; left: 0; top: 2833px; width: 1200px; height: 917px; background: var(--blue); }
  .card { position: absolute; background: var(--navy-card); color: var(--white); padding: 24px 22px; }
  .card h3 { font-size: 27px; font-weight: 500; line-height: 31px; }
  .card p { margin-top: 16px; font-size: 13.5px; line-height: 26px; }

  /* footer */
  .footer { position: absolute; left: 0; top: 3750px; width: 1200px; height: 365px; background: var(--navy); color: var(--white); }
  .footer h4 { position: absolute; font-size: 19px; font-weight: 600; }
  .footer-links li { list-style: none; font-size: 14px; line-height: 32px; color: #d9dce3; }
  .footer-links li::before { content: "- "; }
  .social { position: absolute; top: 3865px; width: 52px; height: 52px; border-radius: 50%; border: 1.5px solid #59606f; }
  .social.on { background: var(--blue-light); border-color: var(--blue-light); }
  .footer-rule { position: absolute; left: 0; top: 4046px; width: 1200px; height: 1px; background: #262d40; }
  .copyright { position: absolute; left: 0; top: 4068px; width: 1200px; text-align: center; font-size: 11.5px; color: #8c92a0; }
  .copyright b { color: #d9dce3; font-weight: 600; }
</style>
</head>
<body>
<div class="page">

  <!-- HERO -->
  <header class="hero" role="img" aria-label="Hikers resting on a mountain ridge at dusk">
    <svg class="abs" style="left:452px;top:281px" width="689" height="392" viewBox="0 0 689 392">
      <rect x="64" y="0" width="561" height="378" rx="14" fill="#1b1e24" stroke="#a9adb4" stroke-width="3"/>
      <circle cx="344.5" cy="14" r="2" fill="#3fd0c4"/>
      <rect x="0" y="374" width="689" height="14" rx="3" fill="#d3d6db"/>
      <rect x="290" y="374" width="109" height="6" rx="3" fill="#a4a8ae"/>
    </svg>
    <div class="photo" role="img" aria-label="Three friends relaxing on a wooden deck facing green mountains"
         style="left:535px;top:304px;width:523px;height:330px;background:linear-gradient(180deg,#c8d2cf 0%,#6f7d63 40%,#4b5a3c 65%,#9b6e49 100%)"></div>

    <div class="brand" style="left:77px;top:30px">
      <span class="brand-name">KESTREL</span>
      <span class="brand-tag">MARKETING VIDEOS MADE FOR YOU</span>
    </div>
    <nav class="nav">
      <a class="active" style="left:398px">Home</a>
      <a style="left:481px">How It Works</a>
      <a style="left:616px">Examples</a>
      <a style="left:725px">Faq</a>
      <a style="left:793px">Contact Us</a>
      <a style="left:913px">Pricing</a>
    </nav>
    <span class="nav-caret"></span>
    <a class="btn" style="left:1019px;top:32px;width:104px;height:51px;font-size:15px">SIGN IN</a>

    <h1 class="abs hero-title">ATTENTION<br>GRABBING VIDEO<br>ADS</h1>
    <p class="abs hero-sub">Delivered in 24 Hours!</p>
    <a class="btn" style="left:78px;top:459px;width:353px;height:51px;font-size:15px">
      GET ONE FREE VIDEO MOCKUP NOW
      <svg width="22" height="12" viewBox="0 0 22 12"><path d="M0 6h20M15 1l5 5-5 5" fill="none" stroke="#fff" stroke-width="1.6"/></svg>
    </a>
  </header>

  <!-- CHANNELS -->
  <section class="channels">
    <h2>We Create Award Winning Promotional Marketing Videos To Ues All Over Ther Web</h2>
  </section>
  <span class="dot" style="left:497px;top:759px;width:64px;height:64px;background:#ee4a3e"></span>
  <span class="dot" style="left:756px;top:748px;width:86px;height:86px;background:linear-gradient(45deg,#f7b03c,#e1306c,#8f3ac4)"></span>
  <span class="dot" style="left:1048px;top:759px;width:64px;height:64px;background:#e23a2f"></span>
  <span class="dot" style="left:631px;top:821px;width:64px;height:64px;background:#1b86c6"></span>
  <span class="dot" style="left:912px;top:821px;width:64px;height:64px;background:#4565b0"></span>
  <span class="dot" style="left:486px;top:884px;width:86px;height:86px;background:#3aaee8"></span>
  <span class="dot" style="left:767px;top:895px;width:64px;height:64px;background:#e32b36"></span>
  <span class="dot" style="left:1037px;top:884px;width:86px;height:86px;background:#1ec0e5"></span>

  <!-- PROMOTE -->
  <h2 class="abs promote-title">PROMOTE ANYTHING</h2>
  <p class="abs promote-kicker">ANYWHERE ON THE WEB</p>
  <p class="abs promote-copy">Still using static image ads with Circlenet, Photoloop, Worklink, Blinkchat advertising platforms? Turn them into VIDEO ADS and get higher conversion rates instantly.</p>
  <div class="photo" role="img" aria-label="Child hugging a giant teddy bear in a toy store aisle"
       style="left:658px;top:1146px;width:542px;height:364px;background:linear-gradient(90deg,#5c6478,#6d7286 50%,#7a6f6c)"></div>
  <svg class="abs" style="left:765px;top:1096px" width="223" height="465" viewBox="0 0 223 465">
    <rect x="1.5" y="1.5" width="220" height="462" rx="28" fill="#fafafa" stroke="#c9ccd1" stroke-width="3"/>
    <circle cx="90" cy="20" r="3" fill="#333"/>
    <rect x="100" y="18" width="34" height="4" rx="2" fill="#333"/>
    <circle cx="111.5" cy="432" r="15" fill="none" stroke="#444" stroke-width="1.5"/>
  </svg>
  <div class="photo" role="img" aria-label="Child carrying a large teddy bear among toy shelves"
       style="left:778px;top:1150px;width:199px;height:355px;background:linear-gradient(180deg,#c7463f 0%,#d9a08a 35%,#b88a5c 60%,#8d6f60 100%)"></div>

  <!-- EXAMPLES -->
  <section class="examples">
    <h2 class="abs section-title" style="left:78px;top:58px">OUR EXAMPLES</h2>
    <span class="abs" style="left:439px;top:83px;width:572px;height:1px;background:var(--line)"></span>
    <span class="arrow" style="left:1033px;top:63px"><svg width="10" height="14"><path d="M8 1L2 7l6 6" fill="none" stroke="#222" stroke-width="1.8"/></svg></span>
    <span class="arrow" style="left:1083px;top:63px"><svg width="10" height="14"><path d="M2 1l6 6-6 6" fill="none" stroke="#222" stroke-width="1.8"/></svg></span>
    <ul class="topics">
      <li style="left:78px;top:136px">Marketing</li>
      <li style="left:78px;top:178px">Memorial Day</li>
      <li style="left:78px;top:219px">Summer</li>
      <li style="left:78px;top:261px">Pets Business</li>
      <li style="left:78px;top:303px">Christmas</li>
      <li style="left:78px;top:344px">New Years</li>
      <li style="left:78px;top:386px">Thanksgiving</li>
      <li style="left:78px;top:428px">Resturants</li>
      <li style="left:264px;top:136px">Halloween</li>
      <li style="left:264px;top:178px">Fitness</li>
      <li style="left:264px;top:219px">Valentines Day</li>
      <li style="left:264px;top:261px">Retail</li>
      <li style="left:264px;top:303px">Labor Day</li>
      <li style="left:264px;top:344px">Real Estate</li>
      <li style="left:264px;top:386px">Insurance</li>
      <li style="left:264px;top:428px">Big Game</li>
    </ul>
    <div class="thumb" role="img" aria-label="Couple in festive skull face paint and costumes"
         style="left:470px;top:138px;width:270px;height:310px;background:linear-gradient(160deg,#8a2a1c,#c2643a 50%,#3c2a22)"></div>
    <div class="thumb" role="img" aria-label="Person holding a carved pumpkin with pink wig"
         style="left:781px;top:138px;width:270px;height:310px;background:linear-gradient(180deg,#e04a8c 0%,#3f5a3a 40%,#c8561e 70%,#6b4b5c)"></div>
    <div class="thumb" role="img" aria-label="Scarecrow costume in a field"
         style="left:1095px;top:138px;width:120px;height:310px;background:linear-gradient(180deg,#5d6a7a,#b76a3a 60%,#6b5a4a)"></div>
  </section>

  <!-- FEATURES -->
  <h2 class="abs section-title" style="left:0;top:2203px;width:1200px;text-align:center">OUR FEATURES</h2>

  <div class="feature" style="left:72px;top:2282px">
    <div class="icon accent"><svg width="52" height="52" viewBox="0 0 52 52" fill="none" stroke="#fff" stroke-width="2"><rect x="4" y="8" width="40" height="40"/><path d="M14 26l9 9L48 6"/></svg></div>
    <h3 class="accent">Done For You</h3>
    <p>We make it super affordable and we DO IT ALL FOR YOU. You'll receive a fully packaged, professi...</p>
  </div>
  <div class="feature" style="left:449px;top:2282px">
    <div class="icon"><svg width="50" height="54" viewBox="0 0 50 54" fill="none" stroke="#fff" stroke-width="1.8"><circle cx="25" cy="20" r="16"/><circle cx="25" cy="20" r="10"/><path d="M20 20l4 4 7-8M15 33l-5 16 8-4 5 6 2-16M35 33l5 16-8-4-5 6"/></svg></div>
    <h3>Premium Content</h3>
    <p>We have access to millions of premium video clips, fully packaged by Award Winning Videographer...</p>
  </div>
  <div class="feature" style="left:826px;top:2282px">
    <div class="icon"><svg width="44" height="54" viewBox="0 0 44 54" fill="none" stroke="#fff" stroke-width="1.8"><rect x="4" y="3" width="36" height="48"/><path d="M11 11h22M11 17h22M16 40l6-16 6 16M14 34l8 6 8-6"/></svg></div>
    <h3>Fully Licensed to you</h3>
    <p>The videos are your property and come with a lifetime license for unlimited sharing and use. Th...</p>
  </div>
  <div class="feature" style="left:72px;top:2542px">
    <div class="icon"><svg width="54" height="50" viewBox="0 0 54 50" fill="none" stroke="#fff" stroke-width="1.8"><rect x="3" y="4" width="40" height="34"/><path d="M10 4v34M36 4v34M14 14h18v14H14zM46 20l6 4-6 4z"/><path d="M26 38v8l14-6"/></svg></div>
    <h3>Perfect Lenght for video ads</h3>
    <p>Our Videos Ads range from 10 seconds to 30 seconds in length with 15 seconds being the sweet sp...</p>
  </div>
  <div class="feature" style="left:449px;top:2542px">
    <div class="icon"><svg width="58" height="40" viewBox="0 0 58 40" fill="none" stroke="#fff" stroke-width="1.8"><rect x="3" y="4" width="40" height="32" rx="6"/><circle cx="23" cy="20" r="9"/><circle cx="23" cy="20" r="4"/><path d="M43 14l12-6v24l-12-6"/></svg></div>
    <h3>Circlenet Video cover</h3>
    <p>We can convert any video to a Circlenet Video Cover for your CN Business page. Additional fees m...</p>
  </div>
  <div class="feature" style="left:826px;top:2542px">
    <div class="icon"><svg width="52" height="52" viewBox="0 0 52 52" fill="none" stroke="#fff" stroke-width="1.8"><path d="M8 10c0 18 14 32 32 32l4-8-8-5-5 4c-6-3-10-7-13-13l4-5-5-8z"/><rect x="28" y="4" width="20" height="14" rx="2"/><path d="M32 9h12M32 13h8"/><circle cx="12" cy="42" r="6"/></svg></div>
    <h3>Best Support</h3>
    <p>Reach out anytime, anywhere. Our team of tech, marketing and video experts are here to help you...</p>
  </div>

  <!-- VIDEO SIZES -->
  <section class="sizes">
    <h2 class="abs section-title" style="left:78px;top:62px;line-height:51px;color:var(--white)">VIDEO SIZES<br>AVAILABLE</h2>
    <div class="photo" role="img" aria-label="Couple embracing at night among glowing candles"
         style="left:77px;top:198px;width:522px;height:365px;background:radial-gradient(circle at 45% 40%,#8a6a44,#3a2a1e 55%,#1a1410)"></div>
    <div class="photo" role="img" aria-label="Two children on a wall looking out over a city skyline"
         style="left:599px;top:125px;width:524px;height:366px;background:linear-gradient(180deg,#9fb8cf 0%,#c9d3d8 35%,#7c8a6e 60%,#3a5c9a 85%,#555 100%)"></div>
    <div class="photo" role="img" aria-label="Woman lying on a knit blanket holding a red rose"
         style="left:599px;top:491px;width:524px;height:366px;background:linear-gradient(135deg,#3a2a24,#7a4a3a 40%,#b9aca4 75%,#d6d1cc)"></div>
  </section>
  <div class="card" style="left:599px;top:2896px;width:262px;height:263px">
    <h3>Wide Screen Videos</h3>
    <p>This size is a standard video size that works best for pretty much anywhere on the web (1080x720) Included with all video purchases</p>
  </div>
  <div class="card" style="left:339px;top:3241px;width:260px;height:260px;padding-top:46px">
    <h3>Square Videos</h3>
    <p>Square Videos that work best on CIRCLENET (Square is 1080 X 1080) Convert any video to this size for an additional fee of $39</p>
  </div>
  <div class="card" style="left:861px;top:3324px;width:262px;height:260px;padding-top:24px">
    <h3>Vertical Videos</h3>
    <p>Vertical Videos that work best on STORIES for Circlenet, Photoloop and Blinkchat (1080 X 1920) Convert any video to this size for an additional fee of $39</p>
  </div>

  <!-- FOOTER -->
  <footer class="footer">
    <div class="brand" style="left:78px;top:66px">
      <span class="brand-name">KESTREL</span>
      <span class="brand-tag">MARKETING VIDEOS MADE FOR YOU</span>
    </div>
    <p class="abs" style="left:78px;top:128px;font-size:13px;font-weight:600">CREATED BY A MARKETER FOR MARKETERS</p>
    <p class="abs" style="left:78px;top:164px;width:320px;font-size:13px;line-height:26px;color:#d9dce3">With Kestrel, you simply let us know what you want to promote and we will have your video ad finished as soon as 24 hours!</p>
    <h4 style="left:439px;top:68px">QUICK LINKS</h4>
    <ul class="footer-links abs" style="left:439px;top:120px">
      <li>How It Works</li>
      <li>Term Of Service</li>
      <li>Privacy Policy</li>
      <li>Cookies Policy</li>
    </ul>
    <h4 style="left:802px;top:68px">FOLLOW US</h4>
  </footer>
  <span class="social on" style="left:799px"></span>
  <span class="social" style="left:861px"></span>
  <span class="social" style="left:925px"></span>
  <span class="social" style="left:987px"></span>
  <span class="social" style="left:1049px"></span>
  <span class="footer-rule"></span>
  <p class="copyright">© <b>KESTREL VIDEO MARKETING FOR YOU</b> - 2019 . All Right Reserved</p>

</div>
</body>
</html>
```